Need a landing page design updated

Need an existing landing page perfected, want it too look similar to one of Quorbel's landing pages in that it flows and is really aesthetically pleasing. The link to the landing page is below. I need this design updated asap. Please take the content directly from the page.

http://verdantmoxfl.com/residential-services/

Target Market(s)

High end residential landscape customers on the gulf coast of Florida (Clearwater area)

Industry/Entity Type

Landscape Gardening

Font styles to use
Sans Serif
Decorative

Requirements
Must have
• I want to keep the written content the same on on the landing page, but would like to work on making both aesthetically appealing to the consumer. This is for high end residential clients on the gulf coast of florida, so think palm trees and sunny beaches with beautiful houses and gorgeous landscapes....look through www.verdantmoxfl.com home page for an example of the houses we landscape.
Nice to have
• Would like it to flow as you scroll similar to Quorbel's landing pages.
• Look at how Quorbel's landing page flows, want similar here.....
• https://www.quorbel.com/zentaphone-v/
Should not have
• this landing page must be beautiful and must make a lot of sense as you scroll, am looking for a work of art....please do not submit generic templates or anything that can be easily done....I need real artistry.

```html
<!DOCTYPE html>
<html lang="en">
<head>
<meta charset="utf-8">
<title>Verdantmox – Residential Landscaping</title>
<link href="https://fonts.googleapis.com/css2?family=Raleway:wght@400;500;600;700&family=Lato:wght@400;700&display=swap" rel="stylesheet">
<style>
:root{
  --teal:#1aa3c9;
  --teal-dark:#1590b3;
  --teal-band:#2bb0d3;
  --ink:#3a3a3a;
  --muted:#6b6b6b;
  --paper:#ffffff;
  --mist:#f4f5f7;
  --slate:#3d4040;
  --grass:#4c7a2a;
}
*{box-sizing:border-box;margin:0;padding:0}
html,body{width:1200px;height:3516px;overflow:hidden}
body{font-family:'Lato',Arial,sans-serif;color:var(--ink);background:var(--paper);position:relative}
.abs{position:absolute}
h2,h3,.display{font-family:'Raleway',Arial,sans-serif}

/* header */
.site-header{left:0;top:0;width:1200px;height:77px;background:var(--paper)}
.brand{left:94px;top:22px;display:flex;align-items:center;gap:10px;font-family:'Raleway',sans-serif;font-weight:600;font-size:28px;color:var(--teal);letter-spacing:1px}
.brand-dot{width:14px;height:14px;border-radius:50%;background:var(--teal)}
.header-contact{right:112px;top:26px;text-align:right;font-size:12px;line-height:18px;color:var(--ink)}
.header-contact .call{color:var(--teal)}
.main-nav{left:0;top:77px;width:1200px;height:36px;background:var(--teal);display:flex;align-items:center;padding-left:124px;gap:26px}
.main-nav a{color:#fff;text-decoration:none;font-size:12px;font-weight:700;letter-spacing:.5px}
.main-nav a.active{color:#0b3d52}

/* hero */
.hero{left:0;top:113px;width:1200px;height:464px;background:linear-gradient(100deg,#3e6b1f 0%,#5b8f2c 35%,#7aa54a 60%,#b9b6a4 75%,#6e9a3a 100%)}
.hero-text{left:230px;top:172px;width:950px;text-align:center;color:#fff}
.hero-text h1{font-family:'Raleway',sans-serif;font-weight:500;font-size:32px;letter-spacing:1px;margin-bottom:12px}
.hero-text p{font-size:16px;line-height:27px}

/* intro */
.intro-copy{left:110px;top:718px;width:530px;text-align:center}
.section-title{font-family:'Raleway',sans-serif;font-weight:700;color:var(--teal);font-size:20px;letter-spacing:.4px;line-height:28px}
.section-sub{font-family:'Raleway',sans-serif;color:var(--teal);font-size:16px;letter-spacing:.3px;line-height:26px}
.body-copy{font-size:13px;line-height:26px;color:var(--muted)}
.intro-copy .body-copy{margin-top:34px}
.photo{border-radius:3px}
.photo-gardener{left:598px;top:628px;width:515px;height:363px;background:linear-gradient(160deg,#7aa83c,#3f6e1e 60%,#2d5216)}

/* compare */
.compare{left:0;top:1043px;width:1200px;height:410px}
.compare-head{left:0;top:1084px;width:1200px;text-align:center;color:#fff}
.compare-head h2{font-weight:700;font-size:16px;letter-spacing:.4px;margin-bottom:10px}
.compare-head p{font-size:13px}
.col-title{font-family:'Raleway',sans-serif;font-weight:600;font-size:22px;color:#fff;letter-spacing:.3px}
.bullets{list-style:none;color:#fff;font-size:11.5px;line-height:19px}
.bullets li{position:relative;padding-left:34px;margin-bottom:18px}
.bullets li::before{content:"";position:absolute;left:0;top:5px;width:8px;height:8px;border:2px solid #fff;border-radius:50%}

/* why */
.why{left:0;top:1453px;width:1200px;height:317px;background:var(--mist)}
.why-copy{left:180px;top:1530px;width:840px;text-align:center}
.why-copy .section-title{font-size:17px}
.why-copy .section-sub{font-size:18px}
.why-copy .body-copy{margin-top:22px;font-size:12.5px}

/* disturb */
.photo-mower{left:87px;top:1823px;width:515px;height:361px;background:linear-gradient(150deg,#6fa03a,#2f5a1a 55%,#8a9a7a)}
.disturb-copy{left:640px;top:1918px;width:445px;text-align:center}
.disturb-copy .section-title{font-size:19px}
.disturb-copy .small-sub{font-family:'Raleway',sans-serif;color:var(--teal);font-size:11px;margin-top:10px}
.disturb-copy .body-copy{margin-top:12px;font-size:12.5px}

/* benefits */
.benefits{left:0;top:2238px;width:1200px;height:392px;background:linear-gradient(180deg,var(--teal-band),var(--teal))}
.benefits h2{position:absolute;left:0;top:56px;width:1200px;text-align:center;color:#fff;font-weight:600;font-size:20px;letter-spacing:.6px}
.benefit{position:absolute;top:118px;width:260px;text-align:center;color:#fff;font-size:13px;line-height:26px}
.benefit .icon{width:112px;height:112px;border-radius:50%;background:#fff;margin:0 auto 28px;display:flex;align-items:center;justify-content:center}

/* more */
.more-copy{left:140px;top:2822px;width:500px}
.more-copy .section-title{font-size:19px;line-height:31px;text-align:center}
.more-copy .body-copy{margin-top:30px;font-size:12.5px}
.photo-basket{left:668px;top:2672px;width:480px;height:363px;background:radial-gradient(ellipse at 50% 55%,#7cb342 0%,#a7c96a 35%,#eef2e6 70%,#ffffff 100%)}

/* cta */
.cta{left:0;top:3063px;width:1200px;height:366px;background:var(--mist)}
.cta-copy{left:0;top:3114px;width:1200px;text-align:center;font-family:'Raleway',sans-serif;color:#222}
.cta-copy p{font-size:20px;line-height:30px}
.cta-copy strong{display:block;font-weight:600;font-size:18px;margin-top:2px}
.field{left:361px;width:488px;height:38px;border:1px solid #c8c8c8;background:#fff;font-size:11px;color:#999;padding:12px 10px}
.btn{left:361px;top:3357px;width:127px;height:34px;background:var(--teal);color:#fff;font-size:11px;display:flex;align-items:center;justify-content:center}

.site-footer{left:0;top:3429px;width:1200px;height:87px;background:var(--teal-band);color:#d8f1f8;text-align:center;font-size:16px;line-height:87px}
</style>
</head>
<body>

<header class="abs site-header">
  <div class="abs brand"><span class="brand-dot"></span>VERDANTMOX</div>
  <div class="abs header-contact"><span class="call">Call Us Now On :</span> 727-555-0148<br>Client Portal | Get A Free Quote</div>
</header>
<nav class="abs main-nav">
  <a class="active">HOME</a><a>ABOUT US</a><a>RESIDENTIAL</a><a>COMMERCIAL</a><a>BLOG</a><a>CONTACT US</a>
</nav>

<section class="abs hero" role="img" aria-label="Lawn mower on a green lawn beside a curved brick garden path"></section>
<div class="abs hero-text">
  <h1>LET’S GUESS :</h1>
  <p>You don’t have an abundance of free time. And, you simply don’t want to spend the little<br>time you have – mowing a lawn and pruning the plants.</p>
</div>

<div class="abs intro-copy">
  <h2 class="section-title">YOU WOULD PROBABLY LIKE TO SPEND</h2>
  <div class="section-sub">THAT TIME THE WAY YOU SHOULD</div>
  <p class="body-copy">Instead. Enjoying the sunset in the privacy of your garden, watching a<br>favorite TV show while lying on a hammock, or throwing an occasional<br>BBQ party with your friends and loved ones.Right?</p>
</div>
<div class="abs photo photo-gardener" role="img" aria-label="Gardener kneeling on a lawn tending shrubs"></div>

<svg class="abs compare" width="1200" height="410" viewBox="0 0 1200 410" aria-hidden="true">
  <defs>
    <linearGradient id="tealFade" x1="0" y1="0" x2="1" y2="0">
      <stop offset="0" stop-color="#1596bd"/><stop offset="1" stop-color="#22a9cf"/>
    </linearGradient>
  </defs>
  <rect width="1200" height="410" fill="#3d4040"/>
  <polygon points="630,0 1200,0 1200,410 560,410" fill="url(#tealFade)"/>
</svg>
<div class="abs compare-head">
  <h2>GETTING AN OUTDOOR AREA OF YOUR DREAMS IS NOT THAT DIFFICULT, NOR EXPENSIVE.</h2>
  <p>You can make this happen by getting a help from a landscaping company that offers tailor-made services.</p>
</div>
<h3 class="abs col-title" style="left:88px;top:1200px">GENERIC LANDSCAPING SERVICES</h3>
<ul class="abs bullets" style="left:90px;top:1258px;width:500px">
  <li>You pay for the bundle of services, regardless of whether you actually need them</li>
  <li>You get a generic service, not adjusted to the specific needs of your<br>outdoor area</li>
  <li>The field team thinks of your property as just another task they have to complete</li>
</ul>
<h3 class="abs col-title" style="left:654px;top:1200px">TAILOR-MADE LANDSCAPING SERVICES</h3>
<ul class="abs bullets" style="left:660px;top:1258px;width:500px">
  <li>You pay only for the services your yard really needs.</li>
  <li>You get your garden’s specific issues solved &amp; specific requirements met</li>
  <li>The field team members take their time working on your property</li>
  <li>They get to learn all about your vision – and make it a reality</li>
</ul>

<section class="abs why"></section>
<div class="abs why-copy">
  <h2 class="section-title">WHY SHOULD YOU CARE THAT VERDANTMOX EMPLOYS THE LEADING</h2>
  <div class="section-sub">INDUSTRY EXPERTS &amp; USES MODERN, ECO-FRIENDLY TECHNICAL SOLUTIONS?</div>
  <p class="body-copy">That is why we’re able to transform your lawn into a green carpet and get your plants in a perfect<br>health. All while keeping your vision and your budget on our minds. That is why our services actu-<br>ally enable you to reduce the operating expenses.</p>
</div>

<div class="abs photo photo-mower" role="img" aria-label="Man pushing a lawn mower through a leafy backyard"></div>
<div class="abs disturb-copy">
  <h2 class="section-title">DO YOU WORRY OUR SERVICES ARE GOING<br>WHILE TRYING TO DISTURB YOU</h2>
  <div class="small-sub">TO UNWIND IN THE PRIVACY OF YOUR OWN GARDEN?</div>
  <p class="body-copy">Our Client Service Operators Build A Schedule Around Your Needs<br>Designed Not To Disturb You At All.</p>
</div>

<section class="abs benefits">
  <h2>MORE BENEFITS OF HAVING A WELL-MAINTAINED YARD:</h2>
  <div class="benefit" style="left:135px">
    <div class="icon"><svg width="56" height="56" viewBox="0 0 56 56"><rect x="8" y="34" width="8" height="14" fill="#1aa3c9"/><rect x="20" y="26" width="8" height="22" fill="#1aa3c9"/><rect x="32" y="30" width="8" height="18" fill="#1aa3c9"/><rect x="44" y="18" width="8" height="30" fill="#1aa3c9"/><polyline points="6,28 20,16 32,22 48,8" fill="none" stroke="#1aa3c9" stroke-width="3"/><polygon points="42,6 52,5 50,14" fill="#1aa3c9"/></svg></div>
    In some cases, a great-looking lawn<br>can increase your property’s value<br>up to 20%.
  </div>
  <div class="benefit" style="left:470px">
    <div class="icon"><svg width="56" height="56" viewBox="0 0 56 56"><polygon points="28,4 52,26 46,26 46,50 10,50 10,26 4,26" fill="#1aa3c9"/><circle cx="28" cy="34" r="10" fill="#fff"/><text x="28" y="39" font-size="14" font-family="Lato,sans-serif" font-weight="700" text-anchor="middle" fill="#1aa3c9">$</text></svg></div>
    Your lawn and plants reduce the energy<br>consumption – countering the warming<br>effects of paved surfaces.
  </div>
  <div class="benefit" style="left:815px">
    <div class="icon"><svg width="56" height="56" viewBox="0 0 56 56"><rect x="14" y="12" width="26" height="32" fill="#1aa3c9"/><rect x="18" y="16" width="3" height="24" fill="#fff"/><rect x="25" y="16" width="3" height="24" fill="#fff"/><rect x="32" y="16" width="3" height="24" fill="#fff"/><rect x="4" y="22" width="10" height="3" fill="#1aa3c9"/><rect x="4" y="31" width="10" height="3" fill="#1aa3c9"/><rect x="40" y="22" width="12" height="3" fill="#1aa3c9"/><rect x="40" y="31" width="12" height="3" fill="#1aa3c9"/></svg></div>
    They act as giant dust filters, increasing<br>air quality, and removing carbon dioxide<br>from the atmosphere.
  </div>
</section>

<div class="abs more-copy">
  <h2 class="section-title">AT VERDANTMOX, WE DO MORE THAN JUST<br>KEEPING YOUR LANDSCAPE IN A PRISTINE STATE.</h2>
  <p class="body-copy">We are delighted with your landscaping, both with the design and implem<br>entation it’s not very often these days that work exceeds expectat ions<br>Verdantmox are efficient, on-time, responsive, provide fair pricing, do<br>outstanding work, have great people</p>
</div>
<div class="abs photo-basket" role="img" aria-label="Wicker basket of green plants with garden tools and twine on a cloth"></div>

<section class="abs cta"></section>
<div class="abs cta-copy">
  <p>So, what’s the next step to enriching your living area?<br>And getting you a garden from your dreams.</p>
  <strong>It’s simple, just book a no-obligations consultation</strong>
</div>
<div class="abs field" style="top:3267px">Name</div>
<div class="abs field" style="top:3312px">Phone OR Email</div>
<div class="abs btn">Get Started</div>

<footer class="abs site-footer">Copyright 2017 Verdantmox All Rights Reserved</footer>

</body>
</html>
```